Mastering Modern Vineyard Management

size of the ad - 8”x 10.75" plus 0.25" bleed
I would like an ad for a magazine that will stand out and make people want to read the ad.
The ad should not be crowded and people reading the ad will be able to read the text.
I would like it to be a creative and modern-day design.
the list of topics should not be the focus of the ad.
the text is attached.
If you decide to use people in the ad then please no ladies.
please note that leave over 1 inch for the bottom of the footer

```html
<!DOCTYPE html>
<html lang="en">
<head>
<meta charset="utf-8">
<title>Mastering Modern Vineyard Management – Course Ad</title>
<link rel="stylesheet" href="https://fonts.googleapis.com/css2?family=Anton&family=Roboto+Condensed:wght@400;700&family=Arimo&display=swap">
<style>
  :root {
    --navy: #07456e;
    --navy-deep: #063f69;
    --ink: #222222;
    --blue-mid: #6f92ad;
    --blue-soft: #a9bdcc;
    --paper: #ffffff;
    --footer: #e3e3e3;
    --rule: #333333;
  }
  * { margin: 0; padding: 0; box-sizing: border-box; }
  html, body { width: 942px; height: 1200px; overflow: hidden; background: var(--paper); }
  .ad {
    position: relative;
    width: 942px;
    height: 1200px;
    overflow: hidden;
    background: linear-gradient(180deg, var(--navy) 0%, #0d4c75 22%, #3f6f92 40%, var(--blue-mid) 52%, var(--blue-soft) 62%, #d6e0e8 68%, var(--paper) 73%, var(--paper) 100%);
    font-family: "Roboto Condensed", "Arial Narrow", sans-serif;
    color: var(--ink);
  }
  .skyline {
    position: absolute;
    left: 107px; top: 39px;
    width: 736px; height: 526px;
    background: linear-gradient(180deg, #f4f7fb 0%, #dbe6f1 60%, #c7d7e8 100%);
    border-radius: 2px;
  }
  .title {
    position: absolute;
    left: 0; width: 942px;
    text-align: center;
    font-family: "Anton", "Impact", sans-serif;
    color: var(--navy-deep);
    text-transform: uppercase;
    line-height: 1;
    letter-spacing: -0.5px;
    text-shadow:
      1px 0 0 #fff, -1px 0 0 #fff, 0 1px 0 #fff, 0 -1px 0 #fff,
      2px 0 0 var(--navy-deep), -2px 0 0 var(--navy-deep), 0 2px 0 var(--navy-deep), 0 -2px 0 var(--navy-deep);
  }
  .title-line-1 { top: 582px; font-size: 58px; }
  .title-line-2 { top: 642px; font-size: 58px; }
  .tagline {
    position: absolute;
    top: 714px; left: 0; width: 942px;
    text-align: center;
    font-weight: 700;
    font-size: 27px;
    letter-spacing: -0.2px;
  }
  .tagline strong { color: var(--navy); }
  .course-rule {
    position: absolute;
    top: 762px; left: 92px; width: 693px;
    display: flex; align-items: center; gap: 4px;
    font-size: 21px; color: var(--navy);
  }
  .course-rule::before, .course-rule::after {
    content: ""; flex: 1; height: 1px; background: var(--rule);
  }
  .topics { position: absolute; top: 812px; left: 92px; }
  .topics h3 { font-size: 17px; font-weight: 700; margin-bottom: 2px; }
  .topics ul { list-style: none; }
  .topics li {
    position: relative;
    padding-left: 19px;
    font-size: 18px;
    line-height: 24px;
  }
  .topics li::before {
    content: ""; position: absolute; left: 1px; top: 9px;
    width: 7px; height: 7px; border-radius: 50%; background: var(--navy);
  }
  .location {
    position: absolute; top: 811px; left: 540px;
    font-size: 17px; font-weight: 700;
  }
  .schedule {
    position: absolute; top: 834px; left: 541px;
    width: 169px; height: 89px;
    background: var(--navy);
    color: #fff;
    padding: 5px 0 0 11px;
    font-size: 17px; line-height: 22px;
  }
  .schedule .start { font-size: 23px; line-height: 30px; margin-top: 2px; }
  .perks { position: absolute; top: 970px; left: 512px; list-style: none; }
  .perks li {
    display: flex; align-items: center; gap: 7px;
    font-size: 24px; font-weight: 700; color: var(--navy);
    height: 38px;
  }
  .perks svg { width: 20px; height: 20px; flex: none; }
  .audience {
    position: absolute; top: 1052px; left: 541px;
    font-family: "Arimo", Arial, sans-serif;
    font-size: 17px; line-height: 21px; color: var(--ink);
  }
  .footer-band {
    position: absolute; left: 0; bottom: 0;
    width: 942px; height: 83px; background: var(--footer);
  }
</style>
</head>
<body>
<main class="ad">
  <div class="skyline" role="img" aria-label="Line illustration of a city skyline with white office towers, trees, clouds and a sun"></div>

  <h1>
    <span class="title title-line-1">Mastering Modern Vineyard</span>
    <span class="title title-line-2">Management</span>
  </h1>

  <p class="tagline">Investing in <strong>KNOWLEDGE</strong> is investing in <strong>OPPORTUNITIES.</strong></p>

  <div class="course-rule">REAL ESTATE COURSE</div>

  <section class="topics">
    <h3>TOPICS:</h3>
    <ul>
      <li>Partial listing</li>
      <li>Real estate investment strategies</li>
      <li>Due diligence</li>
      <li>Financing</li>
      <li>Underwriting</li>
      <li>Property management</li>
      <li>Real estate Legal basics</li>
      <li>Sourcing deals</li>
      <li>Syndication</li>
      <li>Dealing with brokers</li>
      <li>Tax fundamentals</li>
    </ul>
  </section>

  <div class="location">CEDAR HOLLOW</div>
  <div class="schedule">
    <div>10 -TUESDAY</div>
    <div>EVENINGS SESSIONS</div>
    <div class="start">Starting Feb.28</div>
  </div>

  <ul class="perks">
    <li><svg viewBox="0 0 20 20" aria-hidden="true"><path d="M2 11 L7.5 16.5 L18 4" fill="none" stroke="#07456e" stroke-width="3.2" stroke-linecap="round" stroke-linejoin="round"/></svg>Limited Partial Scholarships</li>
    <li><svg viewBox="0 0 20 20" aria-hidden="true"><path d="M2 11 L7.5 16.5 L18 4" fill="none" stroke="#07456e" stroke-width="3.2" stroke-linecap="round" stroke-linejoin="round"/></svg>Early Bird Special</li>
  </ul>

  <p class="audience">For those that started or<br>would like to go into real estate</p>

  <div class="footer-band"></div>
</main>
</body>
</html>
```